Lotstallmart.com Webpage Design

Design Brief for lotstallmart.com (Copy of Brief also in attached Word file)

Name of Website- lotstallmart.com (existing logo and look & feel of website to be changed)

Logo - Finalised. The logo files are attached with the brief as “logo.jpeg”. The “Blue- Grey” version of the logo is for use on lighter backgrounds and the “Orange-White” version of the logo is for use on darker backgrounds. (A full Black version of the logo is also attached). Both versions may be used in different parts of the website. All attached files are in .png format.
Status - The website in functional and is undergoing user trials. However, we want to improve the look & feel of the website so at it seems
a. cotemporary,
b. Easy to Navigate
c. professional and
d. Vibrant.

Please visit ‘lotstallmart.com’ to check out the website and its functionalities – please use it only as a reference for the features & functions to be provided, however the designer should use a ‘Free Hand’ in designing the composition of various parts of the webpage without getting too influenced by the existing design

Objective of the Website ‘lotstallmart.com –
a. It is a portal focussed on listing of ‘Retail’ specific real-estate properties by developers, owners and realty brokers. The properties shall listed under the following four categories-
i. Retail Malls
ii. Shopping Complexes
iii. High-street shops
iv. Retail Warehouses
*refer lotstallmart.com for better clarity

b. The abovementioned properties shall be listed either for ‘Sale’ or ‘rent\lease’ or both

c. Users shall visit the site in case they wish to acquire a retail \ shop space either on ‘sale’ or ‘rent’. These Users would be able to specify the ‘Search Criteria’ through the tool-bars provided on the website – the ‘Search Criteria’ shall comprise of ‘Type of space category’, ‘City’, ‘Locality’, transaction type ie ‘Rent \ Sale’ and ‘Area Range’

d. The main revenue model for the website shall be listing fee ( or advertising charges ) payable by those listing their properties on the website.

Three Main Pages of Website (lotstallmart.com) that need to be designed -
a. Main Home Page (visit the web link - http://lotstallmart.com/ ) - The main home page has the “Search Toolbar” for specifying of Search Criteria by the User. It shall also have the following features & functions-
i. Main Advertising Banner
ii. Featured Projects
iii. New Launches
iv. Toolbar with buttons – ‘Advertise with Us’, ‘Listings Alert’, ‘Mart Wizards’, ‘Advertiser Login’

b. Property Listings Page (visit the web link - http://lotstallmart.com/gurgaon-in-india ) - The List of property options that match the Criteria specified by the ‘User’ get displayed on this page.

c. Property Detail Page - When the ‘User’ clicks on the “More….” Button on the ‘Property Listings Page’ (given in point b. above) the web page with the details of the property opens. (For Example – visit the web link - http://lotstallmart.com/vorne-Shopping-Complex-vorne-quadrion-gurgaon-636 )

Note:- Please refer to attached ‘Shopping’ related images the designer may use them on the website to provide a look & feel of retail if required – either separately or rotate in a single window

Target Market(s)

Retailers & Investors looking for retail space, Real Estate Brokers, Developers

Industry/Entity Type

Advertising

Number of Pages Required

3 page

Requirements
Must have
• Refer to existing site lotstallmart.com -- all the existing functionalities are a must have.
Nice to have
• The Designer may use the retail related images on the website if required for making it more vibrant. Refer attached images Shopping(1-6).jpg

```html
<!DOCTYPE html>
<html lang="en">
<head>
<meta charset="utf-8">
<title>Lotstallmart.com – Retail Space Listings</title>
<link href="https://fonts.googleapis.com/css2?family=Open+Sans:wght@400;600;700&display=swap" rel="stylesheet">
<style>
:root{
  --topbar:#3b3f44;
  --page:#e9eaec;
  --white:#ffffff;
  --ink:#3a3d42;
  --muted:#8a8f96;
  --blue:#1f8fd6;
  --blue-dark:#1677b6;
  --orange:#f7891f;
  --green:#7ab83c;
  --line:#d7d9dc;
  --footer:#3e4247;
  --footer-deep:#2f3236;
  --footer-text:#b7bbc0;
}
*{box-sizing:border-box;margin:0;padding:0}
html,body{width:682px;height:1200px;overflow:hidden}
body{font-family:"Open Sans",Arial,sans-serif;background:var(--page);color:var(--ink);position:relative;font-size:7px}

.top-nav{height:18px;background:var(--topbar);display:flex;align-items:center;padding:0 26px;gap:17px}
.top-nav a{color:#d9dbde;text-decoration:none;font-size:6.5px}

.site-header{height:62px;background:var(--white);display:flex;align-items:center;padding:0 26px;gap:14px}
.brand{display:flex;align-items:center;gap:6px;width:150px}
.brand-mark{width:16px;height:16px;border-radius:50%;background:var(--blue)}
.brand-name{font-size:14px;font-weight:700;color:var(--blue)}
.search-field{width:88px;border-left:1px solid var(--line);padding-left:8px}
.search-field .label{font-size:6px;font-weight:700;text-transform:uppercase;color:var(--ink)}
.search-field .value{font-size:6px;color:var(--muted);margin-top:2px}
.header-actions{margin-left:auto;display:flex;flex-direction:column;gap:4px}
.btn{display:block;font-size:6px;font-weight:700;color:var(--white);text-transform:uppercase;padding:5px 10px;text-align:center;width:96px}
.btn-orange{background:var(--orange)}
.btn-green{background:var(--green)}

.hero{position:absolute;top:80px;left:0;width:682px;height:205px;background:linear-gradient(120deg,#6b4a2c 0%,#b78a58 35%,#d9b07a 55%,#8c6a47 80%,#4d3a2a 100%)}
.search-tab{position:absolute;top:100px;left:0;width:14px;height:110px;background:var(--blue);color:var(--white);font-size:6px;font-weight:700;writing-mode:vertical-rl;transform:rotate(180deg);display:flex;align-items:center;justify-content:center;text-transform:uppercase}

.main{position:absolute;top:297px;left:27px;width:456px}
.panel{background:var(--white);padding:10px 12px 12px;margin-bottom:12px}
.panel-head{display:flex;align-items:center;justify-content:space-between;border-bottom:1px solid var(--line);padding-bottom:6px;margin-bottom:10px}
.panel-title{font-size:8px;font-weight:700;text-transform:uppercase}
.panel-title span{font-weight:400;color:var(--muted);font-size:6px;margin-left:3px}
.panel-arrows{display:flex;gap:4px}
.grid{display:grid;grid-template-columns:repeat(5,1fr);gap:12px 8px}
.card-photo{height:60px;position:relative;background:linear-gradient(180deg,#8fb4d4,#5d7d99)}
.card-photo.alt{background:linear-gradient(180deg,#b7c7d4,#6f8597)}
.card-photo.warm{background:linear-gradient(180deg,#c9b79c,#7e6c57)}
.card-photo .city{position:absolute;left:0;bottom:0;right:0;background:rgba(0,0,0,.45);color:var(--white);font-size:5.5px;padding:2px 4px}
.card-name{font-size:6.5px;font-weight:700;color:var(--orange);margin-top:5px}
.card-type{font-size:5.5px;color:var(--muted);margin-top:1px}
.card-btn{margin-top:5px;border:1px solid var(--line);font-size:5.5px;text-align:center;padding:3px 0;color:var(--ink)}
.card-btn.active{background:var(--orange);border-color:var(--orange);color:var(--white)}

.sidebar{position:absolute;top:215px;left:494px;width:162px}
.cat-list{background:var(--blue);padding:6px 10px}
.cat-item{padding:6px 0;border-bottom:1px solid rgba(255,255,255,.25)}
.cat-item:last-child{border-bottom:0}
.cat-name{font-size:7px;font-weight:700;color:var(--white);text-transform:uppercase}
.cat-sub{font-size:5.5px;color:#cfe6f6;margin-top:2px}
.wizards{background:var(--orange);padding:12px 10px;color:var(--white)}
.wizards h3{font-size:8px;text-transform:uppercase;margin-bottom:5px}
.wizards p{font-size:5.5px;line-height:1.5;margin-bottom:8px}
.input{background:var(--white);height:15px;margin-bottom:6px;font-size:5.5px;color:var(--muted);padding:4px 6px}
.submit{background:var(--blue-dark);color:var(--white);font-size:6px;font-weight:700;width:50px;text-align:center;padding:4px 0;margin-left:auto;text-transform:uppercase}
.side-box{background:var(--white);padding:10px;margin-top:10px}
.side-box h3{font-size:7.5px;text-transform:uppercase;margin-bottom:5px}
.side-box p{font-size:5.5px;color:var(--muted);line-height:1.55;margin-bottom:6px}
.side-box .input{border:1px solid var(--line)}
.submit.blue{background:var(--blue)}

.site-footer{position:absolute;top:1052px;left:0;width:682px;height:130px;background:var(--footer);display:flex;padding:16px 26px;gap:22px}
.foot-col h4{font-size:7px;color:var(--white);text-transform:uppercase;margin-bottom:7px}
.foot-col p,.foot-col li{font-size:5.5px;color:var(--footer-text);line-height:1.6;list-style:none}
.foot-col ul{display:grid;grid-template-columns:1fr 1fr;column-gap:10px}
.social{display:flex;gap:4px;margin-bottom:14px}
.social span{width:12px;height:12px;background:#5b6067}
.foot-brand{display:flex;align-items:center;gap:5px}
.foot-brand .brand-mark{background:var(--orange);width:13px;height:13px}
.foot-brand .brand-name{color:var(--white);font-size:11px}
.copyright{position:absolute;top:1182px;left:0;width:682px;height:18px;background:var(--footer-deep);color:var(--footer-text);font-size:5.5px;display:flex;align-items:center;justify-content:center}
</style>
</head>
<body>
<nav class="top-nav">
  <a>Mall Listings</a><a>Pune</a><a>Chandigarh</a><a>Jaipur</a><a>Noida</a><a>Hyderabad</a><a>Lucknow</a><a>Mumbai</a><a>Kolkata</a><a>Delhi</a><a>News</a><a>Press</a>
</nav>
<header class="site-header">
  <div class="brand"><span class="brand-mark"></span><span class="brand-name">lotstallmart</span></div>
  <div class="search-field"><div class="label">Shopping Space</div><div class="value">Mall, Shop &amp; Store ▾</div></div>
  <div class="search-field"><div class="label">Select City</div><div class="value">Gurgaon ▾</div></div>
  <div class="search-field"><div class="label">Listing Alert</div><div class="value">Get new matches ▾</div></div>
  <div class="header-actions">
    <span class="btn btn-orange">Advertise with us »</span>
    <span class="btn btn-green">New Register Login »</span>
  </div>
</header>

<div class="hero" role="img" aria-label="Family with shopping bags walking through a bright shopping mall"></div>
<div class="search-tab">Select your search</div>

<main class="main">
  <section class="panel">
    <div class="panel-head">
      <div class="panel-title">Featured Retail Projects <span>across India</span></div>
      <div class="panel-arrows">
        <svg width="8" height="8" viewBox="0 0 8 8"><path d="M5 1 2 4l3 3" fill="none" stroke="#8a8f96" stroke-width="1.2"/></svg>
        <svg width="8" height="8" viewBox="0 0 8 8"><path d="M3 1l3 3-3 3" fill="none" stroke="#8a8f96" stroke-width="1.2"/></svg>
      </div>
    </div>
    <div class="grid">
      <article><div class="card-photo" role="img" aria-label="Retail project building"><span class="city">Noida</span></div><div class="card-name">Corvel Arcade</div><div class="card-type">Shopping Complex</div><div class="card-btn active">View Details</div></article>
      <article><div class="card-photo alt" role="img" aria-label="Retail project building"><span class="city">Faridabad</span></div><div class="card-name">Corvel Arcade</div><div class="card-type">Shopping Complex</div><div class="card-btn">View Details</div></article>
      <article><div class="card-photo warm" role="img" aria-label="Retail project building"><span class="city">Gurgaon</span></div><div class="card-name">Corvel Arcade</div><div class="card-type">Shopping Complex</div><div class="card-btn">View Details</div></article>
      <article><div class="card-photo" role="img" aria-label="Retail project building"><span class="city">Gurgaon</span></div><div class="card-name">Corvel Arcade</div><div class="card-type">Shopping Complex</div><div class="card-btn">View Details</div></article>
      <article><div class="card-photo alt" role="img" aria-label="Retail project building"><span class="city">Noida</span></div><div class="card-name">Corvel Arcade</div><div class="card-type">Shopping Complex</div><div class="card-btn">View Details</div></article>
      <article><div class="card-photo warm" role="img" aria-label="Retail project building"><span class="city">Surat</span></div><div class="card-name">Corvel Arcade</div><div class="card-type">Shopping Complex</div><div class="card-btn">View Details</div></article>
      <article><div class="card-photo" role="img" aria-label="Retail project building"><span class="city">Faridabad</span></div><div class="card-name">Corvel Arcade</div><div class="card-type">Shopping Complex</div><div class="card-btn">View Details</div></article>
      <article><div class="card-photo alt" role="img" aria-label="Retail project building"><span class="city">Gurgaon</span></div><div class="card-name">Corvel Arcade</div><div class="card-type">Shopping Complex</div><div class="card-btn">View Details</div></article>
      <article><div class="card-photo warm" role="img" aria-label="Retail project building"><span class="city">Noida</span></div><div class="card-name">Corvel Arcade</div><div class="card-type">Shopping Complex</div><div class="card-btn">View Details</div></article>
      <article><div class="card-photo" role="img" aria-label="Retail project building"><span class="city">Surat</span></div><div class="card-name">Corvel Arcade</div><div class="card-type">Shopping Complex</div><div class="card-btn">View Details</div></article>
    </div>
  </section>

  <section class="panel">
    <div class="panel-head">
      <div class="panel-title">Featured New Launches <span>across India</span></div>
      <div class="panel-arrows">
        <svg width="8" height="8" viewBox="0 0 8 8"><path d="M5 1 2 4l3 3" fill="none" stroke="#8a8f96" stroke-width="1.2"/></svg>
        <svg width="8" height="8" viewBox="0 0 8 8"><path d="M3 1l3 3-3 3" fill="none" stroke="#8a8f96" stroke-width="1.2"/></svg>
      </div>
    </div>
    <div class="grid">
      <article><div class="card-photo alt" role="img" aria-label="New launch building"><span class="city">Surat</span></div><div class="card-name">Corvel Arcade</div><div class="card-type">Shopping Complex</div><div class="card-btn active">View Details</div></article>
      <article><div class="card-photo" role="img" aria-label="New launch building"><span class="city">Faridabad</span></div><div class="card-name">Corvel Arcade</div><div class="card-type">Shopping Complex</div><div class="card-btn">View Details</div></article>
      <article><div class="card-photo warm" role="img" aria-label="New launch building"><span class="city">Gurgaon</span></div><div class="card-name">Corvel Arcade</div><div class="card-type">Shopping Complex</div><div class="card-btn">View Details</div></article>
      <article><div class="card-photo alt" role="img" aria-label="New launch building"><span class="city">Noida</span></div><div class="card-name">Corvel Arcade</div><div class="card-type">Shopping Complex</div><div class="card-btn">View Details</div></article>
      <article><div class="card-photo" role="img" aria-label="New launch building"><span class="city">Gurgaon</span></div><div class="card-name">Corvel Arcade</div><div class="card-type">Shopping Complex</div><div class="card-btn">View Details</div></article>
      <article><div class="card-photo warm" role="img" aria-label="New launch building"><span class="city">Noida</span></div><div class="card-name">Corvel Arcade</div><div class="card-type">Shopping Complex</div><div class="card-btn">View Details</div></article>
      <article><div class="card-photo alt" role="img" aria-label="New launch building"><span class="city">Surat</span></div><div class="card-name">Corvel Arcade</div><div class="card-type">Shopping Complex</div><div class="card-btn">View Details</div></article>
      <article><div class="card-photo" role="img" aria-label="New launch building"><span class="city">Gurgaon</span></div><div class="card-name">Corvel Arcade</div><div class="card-type">Shopping Complex</div><div class="card-btn">View Details</div></article>
      <article><div class="card-photo warm" role="img" aria-label="New launch building"><span class="city">Faridabad</span></div><div class="card-name">Corvel Arcade</div><div class="card-type">Shopping Complex</div><div class="card-btn">View Details</div></article>
      <article><div class="card-photo alt" role="img" aria-label="New launch building"><span class="city">Noida</span></div><div class="card-name">Corvel Arcade</div><div class="card-type">Shopping Complex</div><div class="card-btn">View Details</div></article>
    </div>
  </section>
</main>

<aside class="sidebar">
  <div class="cat-list">
    <div class="cat-item"><div class="cat-name">Retail Malls</div><div class="cat-sub">Find mall space across India</div></div>
    <div class="cat-item"><div class="cat-name">Shopping Complex</div><div class="cat-sub">Units for sale and lease</div></div>
    <div class="cat-item"><div class="cat-name">High Street Shops</div><div class="cat-sub">Prime shop fronts in your city</div></div>
    <div class="cat-item"><div class="cat-name">Retail Warehouses</div><div class="cat-sub">Large format store spaces</div></div>
    <div class="cat-item"><div class="cat-name">Retail Listings</div><div class="cat-sub">Browse every new listing</div></div>
  </div>
  <div class="wizards">
    <h3>Mart Wizards</h3>
    <p>Tell us what retail space you need and our experts will find the best options for you, free of charge, within days.</p>
    <div class="input">Your name</div>
    <div class="input">Email address</div>
    <div class="input">Phone number</div>
    <div class="input">City of interest</div>
    <div class="submit">Send</div>
  </div>
  <div class="side-box">
    <h3>Listing Alert</h3>
    <p>Subscribe for listing alerts and get new retail spaces sent to your inbox.</p>
    <div class="input">Enter your email</div>
    <div class="input">Select space type ▾</div>
    <div class="input">Select city ▾</div>
    <div class="submit blue">Subscribe</div>
  </div>
  <div class="side-box">
    <h3>www.lotstallmart.com</h3>
    <p>Lotstallmart.com is a portal for retail real estate, listing malls, shopping complexes, high street shops and warehouses from developers, owners and brokers.</p>
    <p>Search by city, locality, area range and deal type to find your next store.</p>
  </div>
</aside>

<footer class="site-footer">
  <div class="foot-col" style="width:150px">
    <h4>Editor's Choice</h4>
    <p>Top picks of retail projects this month, chosen by our editors for location, footfall and value for retailers and investors.</p>
  </div>
  <div class="foot-col" style="width:130px">
    <h4>About Lotstallmart</h4>
    <ul><li>About Us</li><li>Retail Malls</li><li>Privacy Policy</li><li>Shopping Complex</li><li>Terms of Use</li><li>High Street Shops</li><li>Contact Us</li><li>Warehouses</li><li>Site Map</li><li>Advertise</li></ul>
  </div>
  <div class="foot-col" style="width:130px">
    <h4>Contact</h4>
    <p>Lotstallmart<br>Vorne Plaza, Sector 9<br>Gurgaon, Haryana<br>Phone: +91 124 555 0192<br>hello@lotstallmart.com</p>
  </div>
  <div class="foot-col">
    <h4>Follow Us</h4>
    <div class="social"><span></span><span></span><span></span><span></span></div>
    <div class="foot-brand"><span class="brand-mark"></span><span class="brand-name">lotstallmart</span></div>
  </div>
</footer>
<div class="copyright">Copyright © 2024 Lotstallmart.com. All rights reserved.</div>
</body>
</html>
```